Health and Fitness Club requires membership pack

We need a membership pack, like this style (http://www.sheetmakersvault.co.uk/images/A4_pocket_folder_round.jpg) a4 sized.

The front of it should contain our logo, the entire thing should be in the style of our brand/concept. On the inside left side there should be space for copy which we will provide once the design has been selected (approximately 500 words).

At the bottom of the left page inside, should be the following:
telephone icon | zqt icon
pixelbrook logo | chirpnet logo | vuo logo | email logo

with the relevant contact details for our company, underneath this should be our website written so that it occupies the entire width of the page.

our website is www. v o r t a g r i p . ae and our logo is attached

i have included a flyer we recently produced to give you an idea of the creative direction of the brand..

```html
<!DOCTYPE html>
<html lang="en">
<head>
<meta charset="utf-8">
<title>Vortagrip Membership Pack – Inside Spread</title>
<link rel="stylesheet" href="https://fonts.googleapis.com/css2?family=Lato:wght@300;700&display=swap">
<style>
  :root {
    --backdrop: #d9d6d2;
    --page-white: #ffffff;
    --page-grey: #e9e8e8;
    --brand-red: #e21e26;
    --band-red: #7b1c1e;
    --band-red-light: #8e2426;
    --pocket-red: #9b1f28;
    --pocket-edge: #b9b6b6;
    --icon-white: #ffffff;
  }
  * { margin: 0; padding: 0; box-sizing: border-box; }
  html, body {
    width: 1200px; height: 795px; overflow: hidden;
    background: var(--backdrop);
    font-family: "Lato", sans-serif;
  }
  .spread {
    position: absolute; left: 64px; top: 26px;
    width: 1072px; height: 743px;
    display: flex;
    box-shadow: 0 4px 14px rgba(0,0,0,.18);
  }
  .page { position: relative; width: 536px; height: 743px; overflow: hidden; }
  .page--copy { background: var(--page-white); }
  .page--pocket { background: var(--page-grey); }

  .brand-mark {
    position: absolute; left: 268px; top: 371px;
    transform: translate(-50%, -50%);
    display: flex; align-items: center; gap: 8px;
  }
  .brand-mark__dot { width: 14px; height: 14px; border-radius: 50%; background: var(--brand-red); }
  .brand-mark__name {
    font-weight: 700; font-size: 20px; letter-spacing: 2px;
    color: var(--brand-red);
  }

  .contact-band {
    position: absolute; left: 0; bottom: 0; width: 100%; height: 85px;
    border-top: 4px solid var(--brand-red);
    background: radial-gradient(ellipse at 50% 40%, var(--band-red-light), var(--band-red) 75%);
  }
  .contact-band__icons {
    position: absolute; top: 12px; left: 0; width: 100%;
    display: flex; justify-content: center; align-items: center; gap: 14px;
  }
  .contact-icon {
    width: 20px; height: 20px; border-radius: 50%;
    background: var(--icon-white);
    display: flex; align-items: center; justify-content: center;
  }
  .contact-icon--mail { background: #5aa342; }
  .contact-label {
    font-size: 11px; font-weight: 700; color: var(--icon-white);
    letter-spacing: .5px;
  }
  .contact-band__web {
    position: absolute; left: 0; right: 0; top: 42px;
    text-align: center;
    font-weight: 300; font-size: 25px; letter-spacing: 4.2px;
    color: var(--icon-white); white-space: pre;
  }

  .pocket { position: absolute; left: 0; top: 0; }
</style>
</head>
<body>
  <main class="spread">
    <section class="page page--copy">
      <div class="brand-mark">
        <span class="brand-mark__dot"></span>
        <span class="brand-mark__name">VORTAGRIP</span>
      </div>

      <footer class="contact-band">
        <div class="contact-band__icons">
          <span class="contact-icon" aria-label="telephone">
            <svg width="12" height="12" viewBox="0 0 24 24"><path fill="#e21e26" d="M6.6 10.8a15 15 0 0 0 6.6 6.6l2.2-2.2c.3-.3.7-.4 1-.2 1.1.4 2.3.6 3.6.6.6 0 1 .4 1 1V20c0 .6-.4 1-1 1A17 17 0 0 1 3 4c0-.6.4-1 1-1h3.5c.6 0 1 .4 1 1 0 1.3.2 2.5.6 3.6.1.3 0 .7-.2 1z"/></svg>
          </span>
          <span class="contact-label">zqt</span>
          <span class="contact-label">pixelbrook</span>
          <span class="contact-label">chirpnet</span>
          <span class="contact-label">vuo</span>
          <span class="contact-icon contact-icon--mail" aria-label="email">
            <svg width="11" height="11" viewBox="0 0 24 24"><rect x="2" y="5" width="20" height="14" rx="2" fill="#fff"/><path d="M2 6l10 7 10-7" fill="none" stroke="#5aa342" stroke-width="2"/></svg>
          </span>
        </div>
        <p class="contact-band__web">www. v o r t a g r i p . ae</p>
      </footer>
    </section>

    <section class="page page--pocket">
      <svg class="pocket" width="536" height="743" viewBox="0 0 536 743">
        <path d="M8 743 C 8 560, 150 451, 322 451 L536 451 L536 743 Z" fill="var(--pocket-edge)"/>
        <path d="M11 743 C 11 563, 152 454, 322 454 L536 454 L536 743 Z" fill="var(--pocket-red)"/>
      </svg>
    </section>
  </main>
</body>
</html>
```